Harbor Ledger Funds Bus card and Logo

I need a logo design and Bus card design. The fund focuses on evaluating and investing in minerals (sub-surface rights) and real estate.

Harbor ledger refers to a book of knowledge that each plebe gets when entering the Kelmont Marine Academy (my alma mater)

Target Market(s)

Investors and financial advisors

Contact Information for Business Card

Simple - perhaps a logo with a theme on book of knowledge

Logo Text

Ex Scientia Imperium

Font styles to use
Serif
Sans Serif

Colors

Designer to choose colors to be used in the design.

Requirements
Must have
• memorable logo that is relatively simple

```html
<!DOCTYPE html>
<html lang="en">
<head>
<meta charset="utf-8">
<title>Harbor Ledger Funds – Business Card</title>
<link href="https://fonts.googleapis.com/css2?family=Montserrat:wght@600&family=Work+Sans:wght@400;500&display=swap" rel="stylesheet">
<style>
  :root {
    --backdrop: #1c1c1c;
    --card: #262626;
    --card-edge: #2e2e2e;
    --accent: #1fb6d6;
    --text: #f2f2f2;
    --muted: #cfcfcf;
    --rule: #bdbdbd;
  }
  * { box-sizing: border-box; margin: 0; padding: 0; }
  html, body {
    width: 1200px; height: 900px; overflow: hidden;
    background: var(--backdrop);
  }
  .stage {
    width: 1200px; height: 900px;
    display: flex; flex-direction: column; align-items: center; justify-content: center;
    gap: 40px;
  }
  .card {
    position: relative;
    width: 680px; height: 388px;
    background: linear-gradient(135deg, var(--card) 0%, var(--card-edge) 100%);
    border-bottom: 6px solid var(--accent);
    box-shadow: 0 14px 30px rgba(0,0,0,.55);
  }
  .wordmark {
    font-family: "Montserrat", sans-serif;
    font-weight: 600;
    color: var(--text);
    text-transform: uppercase;
    display: flex; align-items: center; gap: 12px;
    letter-spacing: 2px;
    line-height: 1.15;
  }
  .wordmark-square {
    width: 16px; height: 16px; background: var(--accent); flex: none;
  }
  .card-front {
    display: flex; align-items: center; justify-content: center;
  }
  .card-front .wordmark { font-size: 36px; }
  .card-back {
    display: flex; align-items: center;
    padding: 0 40px 0 44px;
  }
  .card-back .brand {
    width: 290px;
  }
  .card-back .wordmark { font-size: 27px; }
  .divider {
    width: 1.5px; height: 200px; background: var(--rule);
    margin: 0 34px 0 20px;
  }
  .contact {
    font-family: "Work Sans", sans-serif;
    color: var(--text);
  }
  .contact-name {
    font-family: "Montserrat", sans-serif;
    font-weight: 600;
    color: var(--accent);
    font-size: 30px;
    letter-spacing: 1px;
    text-transform: uppercase;
    line-height: 1;
  }
  .contact-role {
    font-size: 17px; color: var(--muted); margin-top: 2px; letter-spacing: .5px;
  }
  .contact-address {
    font-size: 17px; line-height: 1.35; margin-top: 18px; letter-spacing: .5px;
  }
  .contact-list {
    list-style: none; margin-top: 10px;
    font-size: 17px; line-height: 1.5; letter-spacing: .4px;
  }
  .contact-list li { display: flex; align-items: center; gap: 10px; }
  .contact-list svg { width: 13px; height: 13px; flex: none; }
</style>
</head>
<body>
<main class="stage">

  <section class="card card-front" aria-label="Card front">
    <div class="wordmark"><span class="wordmark-square"></span><span>Harbor Ledger<br>Funds LLC</span></div>
  </section>

  <section class="card card-back" aria-label="Card back">
    <div class="brand">
      <div class="wordmark"><span class="wordmark-square"></span><span>Harbor Ledger<br>Funds LLC</span></div>
    </div>
    <div class="divider"></div>
    <div class="contact">
      <h1 class="contact-name">Daniel Reyes</h1>
      <p class="contact-role">Director</p>
      <p class="contact-address">418 Cedar Hollow Lane<br>Brookvale, CA 95210</p>
      <ul class="contact-list">
        <li>
          <svg viewBox="0 0 16 16" aria-hidden="true"><path d="M4 1.5 6.5 4 5 6c.8 1.8 2.2 3.2 4 4l2-1.5 2.5 2.5-1.5 2C7 13 3 9 2 3.5Z" fill="var(--accent)"/></svg>
          <span>+330 5128-4410</span>
        </li>
        <li>
          <svg viewBox="0 0 16 16" aria-hidden="true"><rect x="1.5" y="3.5" width="13" height="9" fill="none" stroke="var(--accent)" stroke-width="1.5"/><path d="M1.5 3.5 8 9l6.5-5.5" fill="none" stroke="var(--accent)" stroke-width="1.5"/></svg>
          <span>info@harborledgerfunds.com</span>
        </li>
        <li>
          <svg viewBox="0 0 16 16" aria-hidden="true"><circle cx="8" cy="8" r="6.5" fill="none" stroke="var(--accent)" stroke-width="1.4"/><ellipse cx="8" cy="8" rx="2.8" ry="6.5" fill="none" stroke="var(--accent)" stroke-width="1.2"/><path d="M1.5 8h13" stroke="var(--accent)" stroke-width="1.2"/></svg>
          <span>www.harborledgerfunds.com</span>
        </li>
      </ul>
    </div>
  </section>

</main>
</body>
</html>
```